KRL Stationery Design Project

Dear Designers,
We need a new stationery design for company to match our new logo.
Designers should provide a design for the following:
1. Business Card: 3.5x2 Inches.
2. Letterhead: A4 size.
3. Envelops: 25x35.5 Cm.
You can keep the Arabic name at the bottom of the logo Or you can use the separate attached Arabic Name.
Please refer to the attached logo guide for design information.
Sample Business Card information:
Name: Tarek Sowan
Position: Operation Manager
Tel: +966 920007164 Ex. 500
Fax: +966 (3)8842617
Mob: +966 (5)00263817
email: tarek@krl-example.com.sa
URL: www.krl-example.com.sa
Address:
Nakheel Heights, Suite 718
Zayed bin Omar Str.
Khobar, 31847
Saudi Arabia
Updates
Dear All,
Please note, we had uploaded our logo along with Arabic writing in Adobe illustrator format (.ai).
Regards,
Karim
Dear All,
A sample data for the business card had been added as per your request.
Regards,
Karim

```html
<!DOCTYPE html>
<html lang="en">
<head>
<meta charset="utf-8">
<title>KRL Business Card</title>
<link rel="stylesheet" href="https://fonts.googleapis.com/css2?family=Source+Sans+3:wght@400;700&display=swap">
<style>
  :root {
    --stage: #2b2b2b;
    --card: #ffffff;
    --navy: #0e2a4f;
    --ink: #3a3a3a;
    --rule: #b3b3b3;
  }
  html, body {
    margin: 0;
    padding: 0;
    overflow: hidden;
  }
  body {
    width: 960px;
    height: 1200px;
    background: var(--stage);
    position: relative;
    font-family: "Source Sans 3", "Myriad Pro", sans-serif;
    color: var(--ink);
  }
  .card {
    position: absolute;
    left: 60px;
    width: 840px;
    height: 478px;
    background: var(--card);
    border-radius: 30px;
  }
  .card-front { top: 82px; }
  .card-back { top: 643px; }

  .brand {
    position: absolute;
    display: flex;
    align-items: center;
    gap: 22px;
  }
  .brand-mark {
    width: 34px;
    height: 34px;
    background: var(--navy);
  }
  .brand-name {
    font-weight: 700;
    font-size: 120px;
    line-height: 1;
    color: var(--navy);
    letter-spacing: 2px;
  }
  .card-front .brand { left: 60px; top: 60px; }
  .card-back .brand { left: 50%; top: 50%; transform: translate(-50%, -50%); }

  .holder {
    position: absolute;
    right: 32px;
    top: 306px;
    text-align: right;
  }
  .holder-name { font-size: 25px; line-height: 34px; }
  .holder-role { font-size: 19px; line-height: 26px; }

  .rule {
    position: absolute;
    left: 28px;
    right: 34px;
    top: 380px;
    height: 2px;
    background: var(--rule);
  }

  .contact {
    position: absolute;
    top: 396px;
    font-size: 19px;
    line-height: 28px;
    margin: 0;
    padding: 0;
    list-style: none;
  }
  .contact li { display: flex; align-items: center; gap: 6px; white-space: nowrap; }
  .contact-address { left: 27px; }
  .contact-online { left: 350px; }
  .contact-phone { right: 34px; }
  .icon { width: 16px; height: 16px; fill: var(--ink); flex: none; }
  .icon-at { font-size: 18px; font-weight: 700; width: 16px; text-align: center; }
</style>
</head>
<body>

<section class="card card-front">
  <div class="brand">
    <span class="brand-mark"></span>
    <span class="brand-name">KRL</span>
  </div>

  <div class="holder">
    <div class="holder-name">Your Name</div>
    <div class="holder-role">Designation</div>
  </div>

  <div class="rule"></div>

  <ul class="contact contact-address">
    <li>1234, Suite# 123, Street Name</li>
    <li>State NAME, Country Code</li>
  </ul>

  <ul class="contact contact-online">
    <li><span class="icon-at">@</span>info@krl-example.com.sa</li>
    <li>
      <svg class="icon" viewBox="0 0 16 16" aria-hidden="true">
        <circle cx="8" cy="8" r="6.5" fill="none" stroke="currentColor" stroke-width="1.6" style="stroke:#3a3a3a"/>
        <path d="M1.5 8h13M8 1.5c-3 3.5-3 9.5 0 13M8 1.5c3 3.5 3 9.5 0 13" fill="none" stroke="#3a3a3a" stroke-width="1.2"/>
      </svg>www.krl-example.com.sa
    </li>
  </ul>

  <ul class="contact contact-phone">
    <li>
      <svg class="icon" viewBox="0 0 16 16" aria-hidden="true">
        <path d="M1 5c0-2 3-3 7-3s7 1 7 3v1.5h-3.5V5h-7v1.5H1z"/>
        <path d="M3 8h10l1 6H2z"/>
      </svg>123-123-1234
    </li>
    <li>
      <svg class="icon" viewBox="0 0 16 16" aria-hidden="true">
        <rect x="4" y="2" width="8" height="5"/>
        <rect x="1" y="8" width="14" height="6" rx="1"/>
      </svg>123-123-1234
    </li>
  </ul>
</section>

<section class="card card-back">
  <div class="brand">
    <span class="brand-mark"></span>
    <span class="brand-name">KRL</span>
  </div>
</section>

</body>
</html>
```